Fresh, modern, fun business card for pediatric dental practice

Need a business card for fresh, modern, fun pediatric dental practice

Clean look that matches our website's font and colors

We prefer the look of curved corners on business cards

Target Market(s)

parents (mothers) of young children, professionals, mid-high class

Industry/Entity Type

Dental

Contact Information for Business Card

Maplebrook Pediatric Dentistry
482 Quarry Lane
Suite 517
Fernhollow, ST 55501
555.555.0193
www.maplebrookkidsdental.example

Mei-Ran Tsai, DMD
Corinne Walbeck, DMD
(we are working on our email address, but we would like that on the card as well)

Font styles to use
Sans Serif

Requirements
Must have
• All info; we would also like to make cards for individual staff members
• colors from our website and color palatte, attatched
• use same font and design as website for branding
Nice to have
• clean, simple card that has a pop of color
• we would like to see a few designs with our tag line "where smiles get brighter"
• we are not sure if we want to have it on there or not
• we would like to see a few designs incorporating the ribbon graphic on our website where the word WELCOME is

```html
<!DOCTYPE html>
<html lang="en">
<head>
<meta charset="utf-8">
<title>Maplebrook Pediatric Dentistry – Business Card</title>
<link href="https://fonts.googleapis.com/css2?family=Roboto:wght@400;500&family=Roboto+Condensed:wght@700&display=swap" rel="stylesheet">
<style>
  :root {
    --backdrop: #2b2b2b;
    --paper: #f3f3f3;
    --sun: #f0b323;
    --ink: #4a4a4a;
    --rule: #c9c9c9;
    --white: #ffffff;
  }
  * { margin: 0; padding: 0; box-sizing: border-box; }
  html, body {
    width: 1200px; height: 960px; overflow: hidden;
    background: var(--backdrop);
    font-family: "Roboto", Arial, sans-serif;
  }
  .card {
    position: absolute;
    width: 600px; height: 343px;
  }
  .card--front { left: 314px; top: 113px; background: var(--paper); }
  .card--back  { left: 311px; top: 472px; background: var(--sun); }

  .brand {
    position: absolute;
    text-align: center;
    font-family: "Roboto", Arial, sans-serif;
    font-weight: 500;
    line-height: 1;
  }
  .brand__mark {
    display: block;
    margin: 0 auto 12px;
    border-radius: 50%;
  }
  .brand__name { display: block; }
  .brand__line { display: block; }

  .card--front .brand { left: 40px; top: 110px; width: 250px; color: var(--sun); }
  .card--front .brand__mark { width: 44px; height: 44px; background: var(--sun); }
  .card--front .brand__name { font-size: 38px; }
  .card--front .brand__line { font-size: 19px; margin-top: 6px; letter-spacing: 0.5px; }

  .divider {
    position: absolute; left: 304px; top: 84px;
    width: 1px; height: 178px; background: var(--rule);
  }
  .details { position: absolute; left: 331px; top: 84px; }
  .details__dentist {
    font-family: "Roboto Condensed", "Arial Narrow", sans-serif;
    font-weight: 700; font-size: 21px; line-height: 24px;
    color: var(--sun);
  }
  .details__address {
    margin-top: 6px;
    font-size: 14.5px; line-height: 18px; color: var(--ink);
  }
  .details__contact { margin-top: 12px; list-style: none; font-size: 14.5px; line-height: 20px; color: var(--ink); }
  .details__contact li { display: flex; align-items: center; gap: 6px; }
  .details__contact svg { width: 14px; height: 14px; fill: var(--sun); }

  .card--back .brand { left: 0; top: 92px; width: 600px; color: var(--white); }
  .card--back .brand__mark { width: 52px; height: 52px; background: var(--white); }
  .card--back .brand__name { font-size: 46px; }
  .card--back .brand__line { font-size: 23px; margin-top: 6px; letter-spacing: 0.5px; }
  .card--back .site {
    position: absolute; left: 0; top: 295px; width: 600px;
    text-align: center; color: var(--white);
    font-size: 13px; letter-spacing: 4px;
  }
</style>
</head>
<body>
  <section class="card card--front">
    <div class="brand">
      <span class="brand__mark"></span>
      <span class="brand__name">Maplebrook</span>
      <span class="brand__line">pediatric dentistry</span>
    </div>
    <div class="divider"></div>
    <div class="details">
      <p class="details__dentist">Mei-Ran Tsai, DMD</p>
      <p class="details__dentist">Corinne Walbeck, DMD</p>
      <p class="details__address">Maplebrook Pediatric Dentistry<br>482 Quarry Lane<br>Suite 517<br>Fernhollow, ST 55501</p>
      <ul class="details__contact">
        <li>
          <svg viewBox="0 0 24 24" aria-hidden="true"><path d="M6.6 10.8a15.1 15.1 0 0 0 6.6 6.6l2.2-2.2a1 1 0 0 1 1-.25 11.4 11.4 0 0 0 3.6.57 1 1 0 0 1 1 1V20a1 1 0 0 1-1 1A17 17 0 0 1 3 4a1 1 0 0 1 1-1h3.5a1 1 0 0 1 1 1c0 1.25.2 2.45.57 3.57a1 1 0 0 1-.25 1z"/></svg>
          555.555.0193
        </li>
        <li>
          <svg viewBox="0 0 24 24" aria-hidden="true"><path d="M12 2a10 10 0 1 0 0 20 10 10 0 0 0 0-20zm-1 17.9A8 8 0 0 1 4.1 11H7c.2 3 1.4 6 4 8.9zM13 4.1A8 8 0 0 1 19.9 11H17c-.2-3-1.4-6-4-6.9zM9 11c.2-2.6 1.2-5 3-7 1.8 2 2.8 4.4 3 7zm0 2h6c-.2 2.6-1.2 5-3 7-1.8-2-2.8-4.4-3-7z"/></svg>
          maplebrookkidsdental.example
        </li>
      </ul>
    </div>
  </section>

  <section class="card card--back">
    <div class="brand">
      <span class="brand__mark"></span>
      <span class="brand__name">Maplebrook</span>
      <span class="brand__line">pediatric dentistry</span>
    </div>
    <p class="site">www.maplebrookkidsdental.example</p>
  </section>
</body>
</html>
```